Business Card for a Jewellery Brand

Business card for an upscale jewellery brand. Attached is the brand logo and icon and color board. I am looking for two card versions: one for the founder and one is generic. The card should be elegant and convey upscale and premium feel. I am open to both square and rectangle card shapes.

Industry/Entity Type

Jewelry

Contact Information for Business Card

Two cards: (1) Sunela Parvaniya (Founder) (2) General
(1) Sunela Parvaniya card should have Name: Sunela Parvaniya, Title: Founder Email id: sunela@quiremo.com.au. Phone no: +61452913307
(2) Generic card should have Email id: info@quiremo.com.au. Phone no: +61436207518

Requirements
Must have
• Workmark
• ICON
• Phone no
• Email ID
• ABN: 58219740312 (Note: ABN is Business number in Australia)
• Website: www.quiremo.com.au
• Instagram: quiremo_jewellery
• Facebook: @quiremojewellery
Nice to have
• Tagline

```html
<!DOCTYPE html>
<html lang="en">
<head>
<meta charset="utf-8">
<title>Quiremo Business Cards</title>
<link rel="stylesheet" href="https://fonts.googleapis.com/css2?family=Josefin+Sans:wght@400&family=Roboto:wght@400&family=Roboto+Condensed:wght@700&display=swap">
<style>
  :root {
    --backdrop: #e4e4e4;
    --card-dark: #1a1b1d;
    --card-blush: #f3e0da;
    --pattern-tone: #ecd3cc;
    --rose: #d98a8e;
    --text-grey: #5e5e5e;
  }
  * { margin: 0; padding: 0; box-sizing: border-box; }
  html, body {
    width: 1200px; height: 960px; overflow: hidden;
    background: var(--backdrop);
  }
  .canvas { position: relative; width: 1200px; height: 960px; }

  .card {
    position: absolute; width: 600px; height: 342px; overflow: hidden;
  }
  .card--front { left: 302px; top: 129px; background: var(--card-dark); }
  .card--back  { left: 300px; top: 489px; background: var(--card-blush); }

  .wordmark {
    font-family: "Josefin Sans", sans-serif;
    font-weight: 400;
    color: var(--rose);
    letter-spacing: 0.28em;
    white-space: nowrap;
  }

  /* front */
  .front-mark {
    position: absolute; left: 0; right: 0; top: 70px;
    display: flex; flex-direction: column; align-items: center;
  }
  .front-mark .badge { width: 96px; height: 96px; }
  .front-mark .wordmark { margin-top: 40px; font-size: 50px; line-height: 1; padding-left: 0.28em; }

  /* back */
  .pattern-fill {
    position: absolute; inset: 0;
    background: linear-gradient(135deg, var(--card-blush), var(--pattern-tone));
  }
  .back-info { position: absolute; left: 40px; top: 50px; }
  .back-info .wordmark { font-size: 38px; line-height: 1; }
  .person-name {
    margin-top: 22px;
    font-family: "Roboto Condensed", sans-serif; font-weight: 700;
    font-size: 20px; color: var(--rose); text-transform: uppercase; letter-spacing: 0.01em;
  }
  .person-role {
    font-family: "Roboto", sans-serif; font-size: 16px; color: var(--text-grey); margin-top: 2px;
  }
  .contact-list { list-style: none; margin-top: 18px; }
  .contact-list li {
    display: flex; align-items: center; gap: 8px;
    font-family: "Roboto", sans-serif; font-size: 14px; line-height: 18px; color: var(--text-grey);
  }
  .contact-list svg { width: 12px; height: 12px; flex: none; }
  .abn {
    margin-top: 16px;
    font-family: "Roboto", sans-serif; font-size: 14px; color: var(--rose);
  }
  .back-emblem { position: absolute; left: 290px; top: 25px; width: 290px; height: 290px; }
</style>
</head>
<body>
<div class="canvas">

  <section class="card card--front">
    <div class="front-mark">
      <svg class="badge" viewBox="0 0 96 96" aria-hidden="true">
        <circle cx="48" cy="48" r="44" fill="none" stroke="#d98a8e" stroke-width="5"/>
      </svg>
      <div class="wordmark">QUIREMO</div>
    </div>
  </section>

  <section class="card card--back">
    <div class="pattern-fill" role="img" aria-label="Soft blush floral lattice pattern across the card"></div>

    <div class="back-info">
      <div class="wordmark">QUIREMO</div>
      <p class="person-name">Sunela Parvaniya</p>
      <p class="person-role">Founder</p>
      <ul class="contact-list">
        <li>
          <svg viewBox="0 0 12 12" aria-hidden="true"><rect x="3" y="0.5" width="6" height="11" rx="1" fill="none" stroke="#d98a8e" stroke-width="1.2"/><circle cx="6" cy="9.5" r="0.7" fill="#d98a8e"/></svg>
          +61452913307
        </li>
        <li>
          <svg viewBox="0 0 12 12" aria-hidden="true"><rect x="0.5" y="2" width="11" height="8" fill="#d98a8e"/><path d="M0.5 2 L6 6.5 L11.5 2" fill="none" stroke="#f3e0da" stroke-width="1"/></svg>
          sunela@quiremo.com.au
        </li>
        <li>
          <svg viewBox="0 0 12 12" aria-hidden="true"><circle cx="6" cy="6" r="5.5" fill="#d98a8e"/><path d="M0.5 6 H11.5 M6 0.5 C3 3 3 9 6 11.5 C9 9 9 3 6 0.5" fill="none" stroke="#f3e0da" stroke-width="0.8"/></svg>
          www.quiremo.com.au
        </li>
        <li>
          <svg viewBox="0 0 12 12" aria-hidden="true"><rect x="1" y="1" width="10" height="10" fill="#d98a8e"/></svg>
          quiremo_jewellery
        </li>
        <li>
          <svg viewBox="0 0 12 12" aria-hidden="true"><rect x="1" y="1" width="10" height="10" fill="#d98a8e"/></svg>
          @quiremojewellery
        </li>
      </ul>
      <p class="abn">ABN: 58219740312</p>
    </div>

    <svg class="back-emblem" viewBox="0 0 290 290" aria-hidden="true">
      <circle cx="145" cy="145" r="135" fill="none" stroke="#d98a8e" stroke-width="14"/>
    </svg>
  </section>

</div>
</body>
</html>
```